Business Card Design for Marketing Firm

Looking for business card design for higher end marketing firm. Clean but impressionable/trendy. We are a marketing firm that represents manufacturers in the foodservice equipment and supply industry. Our customers are end users such has hotels, restaurants, country clubs, convention centers and casinos as well as distributors of restaurants supplies and equipment, and manufacturers of foodservice equipment and supplies.
Target Market(s)
Hotels, Restaurants, Supply & Equipment Distributors, Foodservice Manufacturers
Industry/Entity Type
Foodservice/Hospitality
Contact Information for Business Card
Name, Title, Contact Number, Email, Website, Social Media, Address
Requirements
Must have
- Clean & Simple but Serious and Impressionable

```html
<!DOCTYPE html>
<html lang="en">
<head>
<meta charset="utf-8">
<title>Harbor Service Reps – Business Card</title>
<link href="https://fonts.googleapis.com/css2?family=Open+Sans:wght@400;700&display=swap" rel="stylesheet">
<style>
  :root {
    --navy: #282a74;
    --white: #ffffff;
    --ink: #1d1d2b;
    --backdrop: #d8d8d6;
  }
  * { margin: 0; padding: 0; box-sizing: border-box; }
  html, body { width: 1200px; height: 801px; overflow: hidden; }
  body {
    background: var(--backdrop);
    font-family: "Open Sans", sans-serif;
    position: relative;
  }
  .card {
    position: absolute;
    top: 245px;
    width: 540px;
    height: 310px;
    border-radius: 18px;
    overflow: hidden;
    box-shadow: 0 6px 18px rgba(0,0,0,0.18);
  }
  .card--front { left: 50px; background: var(--white); }
  .card--back { left: 610px; background: var(--navy); }
  .card__art { position: absolute; inset: 0; }

  .holder { position: absolute; right: 42px; top: 18px; text-align: right; }
  .holder__name { font-weight: 700; font-size: 19px; color: var(--navy); letter-spacing: 0.5px; }
  .holder__title { font-size: 11px; color: var(--ink); margin-top: -2px; }

  .contact {
    position: absolute; right: 28px; top: 118px;
    color: var(--white); font-size: 11.5px; line-height: 19px; text-align: right;
    list-style: none;
  }
  .contact li { display: flex; align-items: center; justify-content: flex-end; gap: 7px; }
  .contact svg { width: 12px; height: 12px; }
  .contact .address { margin-top: 8px; display: block; padding-right: 19px; }

  .wordmark {
    position: absolute;
    display: flex;
    align-items: center;
    font-family: "Open Sans", sans-serif;
    font-weight: 700;
    white-space: nowrap;
  }
  .wordmark__mark { display: block; flex: none; }

  .card--front .wordmark { left: 40px; top: 140px; gap: 10px; font-size: 19px; color: var(--navy); letter-spacing: 0.5px; }
  .card--front .wordmark__mark { width: 14px; height: 14px; background: var(--navy); }

  .card--back .wordmark { left: 0; right: 0; top: 136px; justify-content: center; gap: 14px; font-size: 30px; color: var(--white); letter-spacing: 1px; }
  .card--back .wordmark__mark { width: 22px; height: 22px; background: var(--white); }

  .social { position: absolute; left: 44px; top: 236px; display: flex; gap: 5px; list-style: none; }
  .social li { width: 15px; height: 15px; border-radius: 50%; background: var(--navy); }
</style>
</head>
<body>
  <section class="card card--front" aria-label="Card front">
    <svg class="card__art" viewBox="0 0 540 310" aria-hidden="true">
      <path d="M540,66 C430,70 350,120 300,190 C255,255 200,300 120,310 L540,310 Z" fill="var(--navy)"/>
      <path d="M520,62 C420,74 338,128 290,196 C248,256 196,294 126,302" fill="none" stroke="var(--white)" stroke-width="2.5"/>
      <path d="M510,66 C410,80 328,136 282,200 C242,256 192,292 132,300" fill="none" stroke="var(--navy)" stroke-width="2"/>
      <rect x="510" y="20" width="30" height="30" fill="var(--navy)"/>
    </svg>
    <div class="holder">
      <p class="holder__name">DANIEL REEVE</p>
      <p class="holder__title">Managing Director</p>
    </div>
    <p class="wordmark"><span class="wordmark__mark"></span>HARBOR SERVICE REPS</p>
    <ul class="social" aria-label="Social media">
      <li></li><li></li><li></li><li></li><li></li><li></li>
    </ul>
    <ul class="contact">
      <li>555 010 2040
        <svg viewBox="0 0 12 12" aria-hidden="true"><circle cx="6" cy="6" r="6" fill="#fff"/><path d="M4 3 L5 5 L4.5 5.6 Q5.5 7.2 6.4 7.5 L7 7 L9 8 L8.4 9 Q5 9 3.2 4 Z" fill="var(--navy)"/></svg></li>
      <li>info@harborreps.com
        <svg viewBox="0 0 12 12" aria-hidden="true"><circle cx="6" cy="6" r="6" fill="#fff"/><rect x="3" y="4" width="6" height="4.2" fill="none" stroke="var(--navy)" stroke-width="0.9"/><path d="M3 4 L6 6.4 L9 4" fill="none" stroke="var(--navy)" stroke-width="0.9"/></svg></li>
      <li>www.harborreps.com
        <svg viewBox="0 0 12 12" aria-hidden="true"><circle cx="6" cy="6" r="6" fill="#fff"/><circle cx="6" cy="6" r="3.2" fill="none" stroke="var(--navy)" stroke-width="0.9"/><path d="M2.8 6 H9.2 M6 2.8 V9.2" stroke="var(--navy)" stroke-width="0.8"/></svg></li>
      <li class="address">12 Quay Road, Bayton<br>State, Zip 0000</li>
    </ul>
  </section>

  <section class="card card--back" aria-label="Card back">
    <p class="wordmark"><span class="wordmark__mark"></span>HARBOR SERVICE REPS</p>
  </section>
</body>
</html>
```